Web design project for exciting Australian start-up

Background
We are looking for a creative and talented web design artist to work alongside our market leading web developer.
• You will be required to create a modern and clean design theme for our website, incorporating selected rustic colour scheme elements for our exciting Australian start-up to operate within the coffee industry.
reoccurring work to be expected to flow to the successful designer.
Requirements
• c. 5 - 10 page website
• Landing page
• Log in/ out
• 404 template
• Typography is emphasised
• Please use either a) typemarrow.com, b) free web fonts, c) brindle fonts
• All design elements in vector format
• Preferably with icons for each header title(i.e. about us, how it works etc) but designer have free reign over how the site looks, so might not be applicable
• All pages to be responsive
• Down to eSlab resolution

High level visual design brief attached - additional pages to be worked from base design.

Design inspiration
• We would like to use design elements from the following sources:
http://www.zandrix.com/halcyon/ (Functionality)
Colour scheme refer to logo and complementary style guide

```html
<!DOCTYPE html>
<html lang="en">
<head>
<meta charset="utf-8">
<title>Brewhaven – Online Coffee Market Place</title>
<link rel="stylesheet" href="https://fonts.googleapis.com/css2?family=Open+Sans:wght@400;600;700&family=Arimo:wght@400;700&display=swap">
<style>
:root{
  --orange:#f5873a;
  --ink:#333333;
  --body-text:#4a4a4a;
  --rule:#d6d6d6;
  --footer-bg:#3d3e40;
  --footer-box:#58595b;
  --bottom-bar:#ebebeb;
  --white:#ffffff;
}
*{margin:0;padding:0;box-sizing:border-box}
html,body{width:1200px;height:1187px;overflow:hidden;background:var(--white)}
.page{position:relative;width:1200px;height:1187px;font-family:"Open Sans",sans-serif;color:var(--ink)}

/* header */
.site-header{position:absolute;left:0;top:0;width:1200px;height:108px;background:var(--white)}
.brand{position:absolute;left:88px;top:28px;display:flex;align-items:center;gap:10px;font-family:"Open Sans",sans-serif;font-weight:700;font-size:24px;letter-spacing:1px;color:var(--ink)}
.brand-dot{width:44px;height:44px;border-radius:50%;background:var(--orange)}
.main-nav{position:absolute;top:0;left:484px;display:flex;font-family:"Arimo",sans-serif;font-size:16px;color:var(--ink)}
.main-nav a{color:inherit;text-decoration:none;display:block;height:74px;line-height:4px;padding-top:54px}
.nav-home{width:65px;text-align:center;background:var(--orange);color:var(--white)!important}
.nav-about{margin-left:12px}
.nav-who{margin-left:42px}
.nav-market{margin-left:34px}
.nav-contact{margin-left:33px}
.login-btn{position:absolute;left:1018px;top:44px;width:74px;height:28px;border-radius:4px;background:var(--orange);color:var(--white);font-family:"Arimo",sans-serif;font-size:16px;text-align:center;line-height:28px}

/* hero */
.hero{position:absolute;left:0;top:108px;width:1200px;height:539px;
  background:radial-gradient(ellipse at 30% 65%,#e7d2bd 0,#b7876a 14%,transparent 30%),
             radial-gradient(ellipse at 78% 35%,#b08a5e 0,#7a5538 35%,transparent 60%),
             linear-gradient(180deg,#4a2a1a 0,#5b3320 55%,#3a1d10 100%)}
.hero-title{position:absolute;left:212px;top:52px;color:var(--white);font-weight:700;font-size:29px;line-height:42px;text-shadow:0 1px 3px rgba(0,0,0,.5)}
.hero-cta{position:absolute;left:214px;top:152px;width:202px;height:46px;background:var(--orange);color:var(--white);font-weight:700;font-size:20px;display:flex;align-items:center;justify-content:center;gap:10px}
.slide-arrow{position:absolute;top:226px}
.slide-prev{left:52px}
.slide-next{left:1122px}

/* welcome */
.welcome-title{position:absolute;left:88px;top:685px;color:var(--orange);font-weight:600;font-size:19px}
.welcome-rule{position:absolute;left:88px;top:726px;width:1024px;height:1px;background:var(--rule)}
.welcome-photo{position:absolute;left:88px;top:746px;width:146px;height:146px;border-radius:50%;border:2px solid var(--orange);
  background:radial-gradient(circle at 35% 25%,#f3a04a 0,#b24c1c 30%,#3b1c12 60%),#2a160e}
.welcome-text{position:absolute;left:259px;top:750px;width:853px;font-size:12.6px;line-height:21.8px;color:var(--body-text);text-align:justify}

/* footer */
.footer-accent{position:absolute;left:0;top:939px;width:1200px;height:8px;background:var(--orange)}
.site-footer{position:absolute;left:0;top:947px;width:1200px;height:200px;background:var(--footer-bg);color:var(--white)}
.footer-col{position:absolute;top:18px}
.footer-col h3{color:var(--orange);font-weight:600;font-size:18px;margin-bottom:26px}
.col-info{left:90px}.col-who{left:333px}.col-join{left:563px}.col-contact{left:837px}
.link-list{list-style:none;font-size:13px}
.link-list li{height:24px;display:flex;align-items:center;gap:15px}
.link-list li::before{content:"";border-left:7px solid var(--white);border-top:5px solid transparent;border-bottom:5px solid transparent}
.social-grid{display:grid;grid-template-columns:120px 110px;row-gap:12px;font-size:13px;margin-top:-4px}
.social-item{display:flex;align-items:center;gap:12px}
.social-square{width:24px;height:24px;border-radius:3px;background:var(--footer-box)}
.contact-box{width:275px;height:32px;background:var(--footer-box);border-radius:3px;margin-bottom:6px;padding-left:16px;font-family:"Arimo",sans-serif;font-size:13px;line-height:32px}
.bottom-bar{position:absolute;left:0;top:1147px;width:1200px;height:40px;background:var(--bottom-bar);font-family:"Arimo",sans-serif;font-size:11.5px;color:var(--ink);text-align:center;line-height:40px}
</style>
</head>
<body>
<div class="page">
  <header class="site-header">
    <div class="brand"><span class="brand-dot"></span>BREWHAVEN</div>
    <nav class="main-nav">
      <a class="nav-home" href="#">Home</a>
      <a class="nav-about" href="#">About Us</a>
      <a class="nav-who" href="#">Who we are</a>
      <a class="nav-market" href="#">Market Place</a>
      <a class="nav-contact" href="#">Contact Us</a>
    </nav>
    <div class="login-btn">Login</div>
  </header>

  <section class="hero" role="img" aria-label="Photo of a cup of coffee on a saucer beside a hessian sack of roasted coffee beans and a metal scoop">
    <h1 class="hero-title">AUSTRALIA’S FIRST ONLINE<br>COFFEE MARKET PLACE</h1>
    <div class="hero-cta">WATCH VIDEO
      <svg width="22" height="22" viewBox="0 0 22 22"><circle cx="11" cy="11" r="10" fill="#a8521c"/><path d="M8 6l8 5-8 5z" fill="var(--orange)"/></svg>
    </div>
    <svg class="slide-arrow slide-prev" width="26" height="46" viewBox="0 0 26 46"><path d="M22 3L5 23l17 20" stroke="#fff" stroke-width="5" fill="none"/></svg>
    <svg class="slide-arrow slide-next" width="26" height="46" viewBox="0 0 26 46"><path d="M4 3l17 20L4 43" stroke="#fff" stroke-width="5" fill="none"/></svg>
  </section>

  <h2 class="welcome-title">WELCOME TO BREWHAVEN</h2>
  <div class="welcome-rule"></div>
  <div class="welcome-photo" role="img" aria-label="Photo of a steaming coffee cup in front of a fireplace"></div>
  <p class="welcome-text">Vitae dolores sit et. Vis ex elit reque commune, suas atqui habemus ne mea, per esse errem senserit ei. Vim ne habeo libris reformidans. Vivendum repudiandae ullamcorper ad per, vis dolore tibique ea. Decore partem no cum. Id vis nobis invidunt, ei fugit novum definitiones mei.Vitae dolores sit et. Vis ex elit reque commune, suas atqui habemus ne mea, per esse errem senserit ei. Vim ne habeo libris reformidans. Vivendum repudiandae ullamcorper ad per, vis dolore tibique ea. Decore partem no cum. Id vis nobis invidunt, ei fugit novum definitiones mei.Vitae dolores sit et. Vis ex elit reque commune, suas atqui habemus ne mea, per esse errem senserit ei. Vim ne habeo libris reformidans. Vivendum repudiandae ullamcorper ad per, vis dolore tibique ea. Decore partem no cum. Id vis nobis invidunt.</p>

  <div class="footer-accent"></div>
  <footer class="site-footer">
    <div class="footer-col col-info">
      <h3>Helpful Info</h3>
      <ul class="link-list"><li>About us</li><li>Media enquiries</li><li>Terms &amp; conditions</li><li>Privacy policy</li></ul>
    </div>
    <div class="footer-col col-who">
      <h3>Who We Are</h3>
      <ul class="link-list"><li>How it works</li><li>FAQ</li><li>Contact us</li></ul>
    </div>
    <div class="footer-col col-join">
      <h3>Join Us On</h3>
      <div class="social-grid">
        <div class="social-item"><span class="social-square"></span>Friendlane</div>
        <div class="social-item"><span class="social-square"></span>Workweb</div>
        <div class="social-item"><span class="social-square"></span>Chirper</div>
        <div class="social-item"><span class="social-square"></span>Vidstream</div>
      </div>
    </div>
    <div class="footer-col col-contact">
      <h3>Contact Us</h3>
      <div class="contact-box">Company Adress, Australia</div>
      <div class="contact-box">Phone: +1 (555) 010 2040</div>
      <div class="contact-box">Email: info@brewhaven.com</div>
    </div>
  </footer>
  <div class="bottom-bar">© copy right 2014 Brewhaven | All Rights Reserved</div>
</div>
</body>
</html>
```